Structural Engineering Business Card

Brookvane Drafting does residential house plans for clients in Central Florida. Would like simple but elegant business card that is appropriate for a house plan engineering company. Prefer black business card with black/white them but open to other shades of blue. I uploaded a sample card that I came across that looked good but please come up with your own creative designs.

Contact Information for Business Card

Name, Title, Phone, Email, Address, website

```html
<!DOCTYPE html>
<html lang="en">
<head>
<meta charset="utf-8">
<title>Brookvane Drafting – Business Card</title>
<link rel="stylesheet" href="https://fonts.googleapis.com/css2?family=Poppins:wght@400;600;700&display=swap">
<style>
  :root {
    --backdrop: #e4e4e4;
    --card-dark: #000000;
    --card-light: #ffffff;
    --ink-dark: #111111;
    --ink-light: #ffffff;
    --shadow: rgba(0, 0, 0, 0.28);
  }
  * { margin: 0; padding: 0; box-sizing: border-box; }
  html, body {
    width: 1200px; height: 900px; overflow: hidden;
    background: var(--backdrop);
    font-family: "Poppins", sans-serif;
  }
  .canvas { position: relative; width: 1200px; height: 900px; }
  .card {
    position: absolute; top: 216px; width: 309px; height: 501px;
    box-shadow: 2px 3px 6px var(--shadow);
  }
  .card--front {
    left: 279px; background: var(--card-dark);
    border-radius: 0 54px 0 54px;
    display: flex; align-items: center; justify-content: center;
  }
  .card--back {
    left: 617px; background: var(--card-light);
    border-radius: 54px 0 54px 0;
    color: var(--ink-dark);
  }
  .wordmark {
    font-weight: 700; text-transform: uppercase; line-height: 1.05;
    display: flex; align-items: center; gap: 10px;
  }
  .wordmark__square { width: 14px; height: 14px; flex: none; }
  .wordmark--front { color: var(--ink-light); font-size: 27px; }
  .wordmark--front .wordmark__square { background: var(--ink-light); }
  .wordmark--back {
    position: absolute; left: 37px; top: 160px;
    color: var(--ink-dark); font-size: 23px;
  }
  .wordmark--back .wordmark__square { background: var(--ink-dark); }
  .person { position: absolute; left: 32px; top: 278px; }
  .person__name { font-size: 20px; font-weight: 600; letter-spacing: 0.3px; line-height: 1.1; }
  .person__title { font-size: 14px; font-weight: 400; }
  .contacts { position: absolute; left: 32px; top: 328px; list-style: none; }
  .contacts li {
    display: flex; align-items: center; gap: 9px;
    font-size: 14.5px; line-height: 18px;
  }
  .contacts svg { width: 13px; height: 13px; flex: none; }
  .address {
    position: absolute; left: 33px; top: 398px;
    font-size: 14.5px; line-height: 18px; font-style: normal;
  }
</style>
</head>
<body>
<main class="canvas">
  <section class="card card--front" aria-label="Card front">
    <div class="wordmark wordmark--front">
      <span class="wordmark__square"></span>
      <span>Brookvane<br>Drafting</span>
    </div>
  </section>

  <section class="card card--back" aria-label="Card back">
    <div class="wordmark wordmark--back">
      <span class="wordmark__square"></span>
      <span>Brookvane<br>Drafting</span>
    </div>

    <div class="person">
      <h1 class="person__name">MARCUS HALE</h1>
      <p class="person__title">Managing Director</p>
    </div>

    <ul class="contacts">
      <li>
        <svg viewBox="0 0 24 24" aria-hidden="true"><path fill="#111" d="M6.6 10.8a15.1 15.1 0 0 0 6.6 6.6l2.2-2.2c.3-.3.7-.4 1-.2 1.1.4 2.3.6 3.6.6.6 0 1 .4 1 1V20c0 .6-.4 1-1 1A17 17 0 0 1 3 4c0-.6.4-1 1-1h3.5c.6 0 1 .4 1 1 0 1.3.2 2.5.6 3.6.1.3 0 .7-.2 1z"/></svg>
        044-123 456 789
      </li>
      <li>
        <svg viewBox="0 0 24 24" aria-hidden="true"><path fill="#111" d="M2 5h20v14H2z"/><path fill="none" stroke="#fff" stroke-width="1.8" d="M2 5l10 8 10-8"/></svg>
        info@brookvane.com
      </li>
      <li>
        <svg viewBox="0 0 24 24" aria-hidden="true"><g fill="none" stroke="#111" stroke-width="2"><circle cx="12" cy="12" r="9.5"/><ellipse cx="12" cy="12" rx="4" ry="9.5"/><path d="M2.5 12h19M4 7h16M4 17h16"/></g></svg>
        www.brookvanedrafting.com
      </li>
    </ul>

    <address class="address">
      421, Address line goes here<br>
      45452,Country Name
    </address>
  </section>
</main>
</body>
</html>
```